Trabworth Business Cards

We need a business card design for Trabworth Mining.

This is a B2B company that buys and sells large machinery tires within the coal mining industry. The design should the strong, crisp and masculine. I have uploaded the company logo and rough mock-up of what the back of the card should look like. the front of the card should have the same look/feel as the back. I need editable templates for both the front and the back of the card.

Color scheme should be grey/green/black

Contact information to include on the card:
Name: Dale Pembrose
Title: Managing Director
Phone: 555-314-2069
Address: 1187 Welford #3 Dallas, TX 75290
Email: Dale@Trabworth-example.com

I am also opening a contest for letterhead design. If you submit a business card design, please also submit a letterhead design with the same look/feel. The winner of the business card design will also will the letter head and be paid for both.

Target Market(s)

Procurement men/women in the coal mining industry

Industry/Entity Type

Coal Mining

```html
<!DOCTYPE html>
<html lang="en">
<head>
<meta charset="utf-8">
<title>Trabworth Mining Business Cards</title>
<link href="https://fonts.googleapis.com/css2?family=Open+Sans:wght@300;400;700&display=swap" rel="stylesheet">
<style>
  :root {
    --stage: #e4e4e2;
    --card-black: #0b0b0b;
    --brand-green: #6cb33f;
    --ink-white: #f4f4f4;
    --ink-grey: #c9c9c9;
  }
  * { margin: 0; padding: 0; box-sizing: border-box; }
  html, body {
    width: 1200px;
    height: 1024px;
    overflow: hidden;
    background: var(--stage);
    font-family: "Open Sans", Arial, sans-serif;
  }
  .sheet {
    position: relative;
    width: 1200px;
    height: 1024px;
  }
  .card {
    position: absolute;
    width: 700px;
    height: 400px;
    background: var(--card-black);
    border-bottom: 10px solid var(--brand-green);
    box-shadow: 0 10px 28px rgba(0,0,0,0.25);
    overflow: hidden;
  }
  .card--front { left: 250px; top: 72px; }
  .card--back  { left: 250px; top: 552px; }

  .wordmark {
    color: var(--ink-white);
    font-weight: 700;
    letter-spacing: 2px;
    text-transform: uppercase;
  }
  .card--front .wordmark {
    position: absolute;
    left: 56px;
    top: 70px;
    font-size: 34px;
    line-height: 1;
  }
  .brand-square {
    display: inline-block;
    width: 22px;
    height: 22px;
    background: var(--brand-green);
    margin-right: 14px;
    vertical-align: 2px;
  }

  .contact {
    position: absolute;
    left: 56px;
    top: 170px;
    font-size: 19px;
    line-height: 1.5;
    color: var(--ink-white);
    font-weight: 400;
  }
  .contact__name { color: var(--ink-grey); font-weight: 300; }
  .contact__title { color: var(--brand-green); margin-bottom: 14px; }
  .contact__label { color: var(--brand-green); }

  .card--back .wordmark {
    position: absolute;
    left: 0;
    right: 0;
    top: 176px;
    text-align: center;
    font-size: 40px;
    line-height: 1;
  }
</style>
</head>
<body>
<main class="sheet">
  <section class="card card--front" aria-label="Business card front">
    <div class="wordmark"><span class="brand-square"></span>Trabworth Mining</div>
    <div class="contact">
      <p class="contact__name">Dale Pembrose</p>
      <p class="contact__title">Managing Director</p>
      <p><span class="contact__label">Phone:</span> 555-314-2069</p>
      <p><span class="contact__label">Address:</span> 1187 Welford #3 Dallas, TX 75290</p>
      <p><span class="contact__label">Email:</span> Dale@Trabworth-example.com</p>
    </div>
  </section>

  <section class="card card--back" aria-label="Business card back">
    <div class="wordmark"><span class="brand-square"></span>Trabworth Mining</div>
  </section>
</main>
</body>
</html>
```